"Harbor Builders" is a residential building company and needs a new business card design and may re

We would like a redesign based on the existing logo, and would like to see a new font as well. We are bespoke home builders who build sustainable energy efficient homes.

Industry/Entity Type

Construction

Contact Information for Business Card

Business card size 40mm x 90mm

Colors

Designer to choose colors to be used in the design.

```html
<!DOCTYPE html>
<html lang="en">
<head>
<meta charset="utf-8">
<title>Harbor Builders – Business Card</title>
<link href="https://fonts.googleapis.com/css2?family=Source+Sans+3:wght@400;600;700&family=PT+Sans+Narrow:wght@400;700&display=swap" rel="stylesheet">
<style>
  :root {
    --backdrop: #8f8f8f;
    --card-light: #dddddd;
    --card-dark: #070808;
    --ink: #141414;
    --ink-soft: #2b2b2b;
    --leaf: #a3bd31;
    --logo-light: #e2e2e2;
  }
  * { margin: 0; padding: 0; box-sizing: border-box; }
  html, body {
    width: 1105px; height: 1200px; overflow: hidden;
    background: var(--backdrop);
    font-family: "Source Sans 3", "Helvetica Neue", Arial, sans-serif;
  }
  .card {
    position: absolute;
    left: 183px;
    width: 747px;
    height: 427px;
  }
  .card--front { top: 119px; background: var(--card-light); color: var(--ink); }
  .card--back  { top: 636px; background: var(--card-dark); }

  /* front: brand mark area on the left */
  .brand-corner {
    position: absolute; left: 0; top: 0;
    width: 420px; height: 290px;
    display: flex; align-items: center; gap: 20px;
    padding-left: 44px;
  }
  .brand-corner__square { width: 56px; height: 56px; background: var(--leaf); flex: none; }
  .brand-corner__name {
    font-size: 40px; font-weight: 700; color: var(--ink); letter-spacing: -0.5px;
    white-space: nowrap;
  }

  /* front: contact block */
  .contact {
    position: absolute; right: 40px; top: 160px;
    text-align: right;
  }
  .contact__name {
    font-size: 26px; font-weight: 700; color: var(--ink); line-height: 32px; margin-bottom: 8px;
  }
  .contact__company { font-size: 17px; font-weight: 600; color: var(--ink-soft); line-height: 22.5px; }
  .contact__address { font-size: 17px; color: var(--ink-soft); line-height: 22.5px; }
  .contact__lines { margin-top: 10px; }
  .contact__line {
    display: flex; justify-content: flex-end; align-items: center; gap: 10px;
    font-size: 17px; color: var(--ink-soft); line-height: 24.5px;
  }
  .contact__icon { width: 16px; height: 16px; flex: none; }
  .contact__legal {
    margin-top: 12px;
    font-family: "PT Sans Narrow", "Arial Narrow", sans-serif;
    font-size: 15px; color: var(--ink-soft);
  }
  .contact__legal b { font-weight: 700; }

  /* back: brand lockup */
  .lockup {
    position: absolute; left: 0; right: 0; top: 0; bottom: 0;
    display: flex; align-items: center; justify-content: center; gap: 22px;
  }
  .lockup__square { width: 58px; height: 58px; background: var(--leaf); }
  .lockup__name {
    font-size: 56px; font-weight: 600; color: var(--logo-light); letter-spacing: -0.5px;
  }
</style>
</head>
<body>

<section class="card card--front">
  <div class="brand-corner">
    <span class="brand-corner__square"></span>
    <span class="brand-corner__name">Harbor Builders</span>
  </div>

  <div class="contact">
    <div class="contact__name">Daniel Moretti</div>
    <div class="contact__company">Harbor Builders Pty Ltd</div>
    <div class="contact__address">PO Box 2480 Eastgate</div>
    <div class="contact__address">LPO Bayview WA 6099</div>

    <div class="contact__lines">
      <div class="contact__line">0400 123 987
        <svg class="contact__icon" viewBox="0 0 16 16" aria-hidden="true">
          <rect x="4" y="1" width="8" height="14" rx="1.5" fill="none" stroke="#141414" stroke-width="1.6"/>
          <line x1="7" y1="12.5" x2="9" y2="12.5" stroke="#141414" stroke-width="1.4"/>
        </svg>
      </div>
      <div class="contact__line">daniel@harborbuilders.com.au
        <svg class="contact__icon" viewBox="0 0 16 16" aria-hidden="true">
          <rect x="1" y="3.5" width="14" height="9" fill="#141414"/>
          <polyline points="1.5,4 8,9 14.5,4" fill="none" stroke="#dddddd" stroke-width="1.2"/>
        </svg>
      </div>
      <div class="contact__line">www.harborbuilders.com.au
        <svg class="contact__icon" viewBox="0 0 16 16" aria-hidden="true">
          <circle cx="8" cy="8" r="7" fill="#141414"/>
          <ellipse cx="8" cy="8" rx="3" ry="7" fill="none" stroke="#dddddd" stroke-width="1"/>
          <line x1="1" y1="8" x2="15" y2="8" stroke="#dddddd" stroke-width="1"/>
        </svg>
      </div>
    </div>

    <div class="contact__legal"><b>Registration:</b> 40871 &nbsp;<b>ABN:</b> 52 904 316 278</div>
  </div>
</section>

<section class="card card--back">
  <div class="lockup">
    <span class="lockup__square"></span>
    <span class="lockup__name">harbor builders</span>
  </div>
</section>

</body>
</html>
```